Website Redesign Brief for Breezeline Climate Services WA

Creating a clear and concise brief for designers to redesign your website, https://breezelineclimatewa.com.au/, is essential to ensure the project aligns with your vision for a more energetic, friendly, optimistic, and user-friendly website. Below is a sample brief tailored to your request, balancing specificity with flexibility to allow designers to bring their creativity to the table.

Website Redesign Brief for Breezeline Climate WA
1. Project Overview

We are seeking a redesign of our website, https://breezelineclimatewa.com.au/, to create a vibrant, engaging, and user-friendly online presence that reflects our brand’s commitment to providing top-notch air conditioning services in Western Australia. The redesigned website should feel energetic, friendly, and optimistic while maintaining professionalism and improving user experience.
2. Goals and Objectives

Enhance Brand Perception: Convey a modern, approachable, and positive brand identity that resonates with both residential and commercial clients.
Improve User Experience: Simplify navigation, improve accessibility, and ensure a seamless experience across devices (desktop, tablet, mobile).
Increase Engagement: Encourage visitors to explore services, request quotes, and contact us through clear calls-to-action (CTAs).
Boost Conversion Rates: Make it easier for users to find information and take action (e.g., booking services or inquiries).
Showcase Expertise: Highlight our professional air conditioning services, experience, and customer satisfaction in an inviting way.

3. Target Audience

Primary Audience: Homeowners and small business owners in Western Australia seeking air conditioning installation, maintenance, or repair services.
Secondary Audience: Property managers, commercial clients, and real estate professionals looking for reliable HVAC solutions.
Demographics: Ages 25–65, mix of tech-savvy and non-tech-savvy users, located primarily in Perth and surrounding areas.
User Needs: Clear information about services, transparent pricing, easy contact options, and reassurance of quality and reliability.

4. Design Preferences

Tone and Style:

Energetic: Use bold, vibrant colors (e.g., blues, whites, and pops of warm tones like orange or yellow) to evoke energy and optimism.
Friendly: Incorporate approachable language, welcoming imagery, and a clean, uncluttered layout.
Optimistic: Highlight positive customer outcomes (e.g., comfort, energy savings) through visuals and messaging.
Professional yet approachable: Maintain credibility as a trusted service provider while avoiding a cold or overly corporate feel.

Visual Elements:

Use high-quality images of happy customers, comfortable homes/offices, and modern air conditioning units.
Incorporate subtle animations or micro-interactions to add energy (e.g., hover effects on buttons or smooth scrolling).
Avoid overly complex graphics that may slow down the site or distract from usability.

Typography: Clean, modern fonts that are easy to read. Use larger, bold headings for hierarchy and warmth.
Inspiration: Websites like https://www.vorlex.com.au/ (clean and professional) or https://www.tandoraclimatech.com.au/ (user-friendly and modern) but with a more vibrant and welcoming vibe.

5. Functional Requirements

User-Friendly Navigation: Simplify the menu structure to make key pages (e.g., Services, About Us, Contact) easily accessible.
Mobile Responsiveness: Ensure the site is fully optimized for mobile devices, with fast load times and intuitive touch interactions.
Key Features:

Prominent CTAs for requesting quotes, booking services, or contacting the team.
A clear service overview with icons or visuals for each service (e.g., installation, repairs, maintenance).
A testimonials section to showcase customer satisfaction.
An easy-to-use contact form with minimal fields.
Integration with Google Maps for location-based services or office directions.

SEO and Performance: Optimize for search engines (e.g., keywords like “air conditioning Perth”) and ensure fast loading speeds.
Accessibility: Follow WCAG guidelines to ensure the site is usable for all visitors, including those with disabilities.

6. Content Guidance

Existing Content: Review and refine current content from https://breezelineclimatewa.com.au/ to make it concise, engaging, and aligned with the friendly tone.
New Content Ideas:

Add a “Why Choose Us” section highlighting expertise, customer service, and eco-friendly solutions.
Include a FAQ page to address common customer questions.
Create a blog section for tips on air conditioning maintenance or energy efficiency (optional).

Tone of Voice: Conversational, reassuring, and positive. Avoid technical jargon unless clearly explained.

7. Technical Considerations

Platform: Open to recommendations (e.g., WordPress, Wix, or custom-built) but prioritize ease of maintenance and scalability.
Integrations: Ensure compatibility with existing tools (e.g., Google Analytics, CRM for quote requests, or booking systems).
Domain and Hosting: Retain current domain (breezelineclimatewa.com.au); hosting recommendations welcome.
Timeline: Initial design concepts within [insert timeline, e.g., 2–3 weeks], with full redesign completed by [insert deadline, e.g., 6–8 weeks].
Budget: [Insert budget range or state “flexible, please provide a quote”].

8. Deliverables

Wireframes and mockups for homepage, service pages, and contact page.
Fully responsive website design with all necessary pages.
Style guide (colors, fonts, imagery guidelines).
CMS setup (if applicable) with basic training for content updates.
Testing and optimization for performance and SEO.

9. Success Metrics

Increased time on site and reduced bounce rate.
Higher conversion rates for quote requests and contact form submissions.
Positive user feedback on ease of navigation and overall experience.
Improved search engine rankings for key terms within [insert timeframe, e.g., 3 months].

10. Additional Notes

Please provide a portfolio of similar projects or examples of user-friendly, vibrant websites.
We are open to creative suggestions to make the website stand out in the HVAC industry.
Regular progress updates and collaboration during the design process are appreciated.
Updates

designers are asking for more time

few have requested an extension. I Have extended

Target Market(s)

Primary Audience: Homeowners and small business owners in Western Australia seeking air conditioning installation, maintenance, or repair services. Secondary Audience: Property managers, commercial clients, and real estate professionals looking for reliable HVAC solutions. Demographics: Ages 25–65, mix of tech-savvy and non-tech-savvy users, located primarily in Perth and surrounding areas. User Needs: Clear information about services, transparent pricing, easy contact options, and reassurance of quality and reliability.

Industry/Entity Type

Air Conditioning and Refrigeration (HVAC & R)

Coding

Coded - Design and coding required

Colors
0054AA
0677BA
7BADD7
CADEEF
E8F1F8
59FF00
82FF00
B8FF75
E3FFCB
F4FFEA
F0912C
F2A743
F7CA91
FBE8D2
FDF5EE
EE7325
F08F49
F5BC92
FAE3D3
FDF4ED

Requirements
Must have
• Must have all my current information I currently have on my web page.
Nice to have
• A sales page for people to buy products online

```html
<!DOCTYPE html>
<html lang="en">
<head>
<meta charset="utf-8">
<title>Breezeline Climate Services WA – Air Conditioning Repairs, Service & Installations</title>
<link href="https://fonts.googleapis.com/css2?family=Poppins:wght@400;500;600;700;800&display=swap" rel="stylesheet">
<style>
:root{
  --navy:#1c2b5e;
  --navy-deep:#1d2a57;
  --blue:#0677BA;
  --blue-dark:#0054AA;
  --blue-soft:#7BADD7;
  --orange:#EE7325;
  --orange-light:#F0912C;
  --orange-pale:#FAE3D3;
  --red:#d8322e;
  --grey:#f2f2f2;
  --text:#555b66;
  --white:#ffffff;
}
*{margin:0;padding:0;box-sizing:border-box}
html,body{width:1200px;height:4721px;overflow:hidden}
body{font-family:"Poppins",sans-serif;color:var(--text);background:var(--white);position:relative}
.abs{position:absolute}
a{color:inherit;text-decoration:none}

/* Header */
.nav-bar{left:66px;top:58px;width:1070px;height:63px;background:var(--white);border-radius:32px;box-shadow:0 4px 18px rgba(0,0,0,.12);z-index:5}
.brand{left:108px;top:24px;width:126px;height:126px;border-radius:50%;background:var(--white);border:4px solid var(--orange);z-index:6;display:flex;align-items:center;justify-content:center;text-align:center;font-weight:700;font-size:13px;line-height:1.2;color:var(--navy);padding:14px}
.nav-links{left:365px;top:80px;display:flex;gap:26px;font-size:13px;color:var(--navy);z-index:6;align-items:center}
.home-ico{width:16px;height:14px}
.btn{display:inline-flex;align-items:center;justify-content:center;border-radius:30px;font-weight:600;color:var(--white);background:linear-gradient(90deg,var(--red),var(--orange-light))}
.btn-quote{left:964px;top:62px;width:166px;height:54px;font-size:15px;z-index:6;border:3px solid var(--white);box-shadow:0 0 0 2px var(--orange)}

/* Hero */
.hero{left:0;top:0;width:1200px;height:900px;background:linear-gradient(115deg,#1d3f86 0%,#2b5ea4 40%,#8aa3c4 70%,#c9ced6 100%)}
.hero-photo{left:560px;top:140px;width:640px;height:700px;background:radial-gradient(ellipse at 55% 45%,#b9bec6 0%,#8f98a6 45%,rgba(120,135,160,0) 75%)}
.hero h1{left:86px;top:262px;width:660px;font-size:43px;line-height:58px;font-weight:800;color:var(--white);letter-spacing:-.5px}
.hero-text{left:86px;top:452px;width:490px;font-size:14px;line-height:22px;color:var(--white)}
.btn-book{left:86px;top:542px;width:176px;height:48px;font-size:14px}
.swoosh{left:0;width:1200px}

/* About */
.about-photo{left:165px;top:855px;width:442px;height:442px;border-radius:50%;background:radial-gradient(circle at 45% 40%,#e8e4df 0%,#cbb9a6 55%,#a35b3b 100%);box-shadow:0 20px 40px rgba(0,0,0,.12)}
.tag{display:inline-block;border:1.5px solid var(--orange);border-radius:20px;font-size:8px;font-weight:600;color:var(--orange);text-transform:uppercase;padding:7px 16px;background:var(--white)}
.about-tag{left:661px;top:903px}
.h2{font-weight:700;color:var(--navy)}
.about h2{left:661px;top:946px;font-size:33px}
.about-text{left:661px;top:1000px;width:390px;font-size:13.5px;line-height:22px}
.contact-mini{top:1136px;display:flex;gap:12px;align-items:center;font-size:10.5px;color:var(--navy)}
.contact-mini .dot{width:28px;height:28px;border-radius:50%}
.contact-mini b{display:block;font-weight:600;font-size:10.5px}
.btn-more{left:661px;top:1188px;width:174px;height:52px;font-size:13.5px}

/* Services */
.svc-tag{left:158px;top:1473px}
.services h2{left:158px;top:1510px;font-size:34px}
.svc-text{left:158px;top:1564px;width:360px;font-size:13.5px;line-height:22px}
.card{background:var(--white);border:1.5px solid var(--blue);border-radius:14px;display:flex;align-items:center;gap:14px;padding:0 14px;font-size:12px;line-height:17px;color:var(--navy);font-weight:500;box-shadow:0 6px 18px rgba(6,119,186,.1)}
.card.feature{border-color:var(--orange);flex-direction:column;align-items:flex-start;padding:8px;gap:12px;background:#fffaf6}
.card-photo{width:212px;height:158px;border-radius:8px;background:linear-gradient(180deg,#b7c4cc 0%,#8d9aa0 55%,#6f7a72 100%)}
.ico{width:52px;height:52px;border-radius:8px;background:linear-gradient(135deg,var(--blue-dark),var(--blue));flex:none;display:flex;align-items:center;justify-content:center}

/* Why choose */
.why-bg{left:0;top:2000px;width:1200px;height:580px;background:var(--grey)}
.why-tag{left:547px;top:1975px}
.why h2{left:0;width:1200px;top:2012px;text-align:center;font-size:33px}
.reason{width:170px;text-align:center}
.ring{width:110px;height:110px;margin:0 auto;border-radius:50%;border:2px solid transparent;border-top-color:var(--orange);border-left-color:var(--orange);position:relative;display:flex;align-items:center;justify-content:center}
.num{width:84px;height:84px;border-radius:50%;background:linear-gradient(135deg,var(--blue),var(--blue-dark));color:var(--white);font-weight:700;font-size:32px;display:flex;align-items:center;justify-content:center;box-shadow:0 6px 14px rgba(0,84,170,.3)}
.num.warm{background:linear-gradient(135deg,var(--orange-light),var(--red))}
.arrow{position:absolute;right:-34px;top:38px}
.reason h3{margin-top:10px;font-size:15px;line-height:20px;color:var(--navy);font-weight:600}
.reason p{margin-top:10px;font-size:12.5px;line-height:19px}

/* Testimonials */
.testi-tag{left:548px;top:2455px}
.testi h2{left:0;width:1200px;top:2494px;text-align:center;font-size:32px}
.quote-badge{left:548px;top:2568px;width:104px;height:104px;border-radius:50%;background:linear-gradient(135deg,var(--orange-light),var(--red));display:flex;align-items:center;justify-content:center;box-shadow:0 8px 20px rgba(238,115,37,.35)}
.testi-text{left:300px;width:600px;top:2690px;text-align:center;font-size:17px;line-height:27px;color:#4b5160}
.stars{left:0;width:1200px;top:2796px;text-align:center;color:var(--orange);font-size:22px;letter-spacing:5px}
.testi-name{left:0;width:1200px;top:2826px;text-align:center;font-size:18px;font-weight:600;color:var(--navy)}
.dots{left:584px;top:2862px;display:flex;gap:6px}
.dots span{width:6px;height:6px;border-radius:50%;background:#d4d4d4}
.dots span:first-child{background:var(--navy)}
.divider{left:152px;top:2937px;width:896px;height:1px;background:#e3e3e3}

/* FAQ */
.faq h2{left:134px;top:3052px;font-size:34px}
.faq-list{left:134px;top:3106px;width:416px}
.faq-item{height:53px;border-bottom:1px solid #e6e6e6;display:flex;align-items:center;justify-content:space-between;padding:0 14px;font-size:13px;color:var(--navy);font-weight:500}
.faq-item span{color:var(--orange);font-size:14px}
.faq-visual{left:605px;top:3004px;width:448px;height:404px;background:radial-gradient(ellipse at 50% 55%,#ffffff 0%,#eef1f4 40%,rgba(230,120,60,.25) 70%,rgba(255,255,255,0) 78%)}

/* Contact */
.contact-card{left:145px;top:3499px;width:417px;height:440px;border-radius:28px;background:linear-gradient(150deg,var(--red) 0%,#e85a2a 50%,var(--orange-light) 100%);box-shadow:0 20px 40px rgba(216,50,46,.25)}
.contact-card h2{position:absolute;left:50px;top:40px;font-size:42px;font-weight:700;color:var(--white)}
.field{position:absolute;left:49px;width:331px;height:42px;background:var(--white);border-radius:22px;padding:11px 30px;font-size:14px;font-weight:500;color:var(--navy)}
.field.area{height:146px;border-radius:20px}
.submit{position:absolute;left:49px;top:385px;width:331px;height:42px;border-radius:22px;background:linear-gradient(90deg,var(--blue-dark),var(--blue));color:var(--white);font-size:14px;font-weight:600;display:flex;align-items:center;justify-content:center}
.cta h2{left:630px;top:3614px;font-size:33px}
.cta p{left:630px;top:3676px;width:440px;font-size:13px;line-height:22px}
.btn-sm{height:40px;font-size:12.5px;top:3786px}
.btn-blue{background:linear-gradient(90deg,var(--blue-dark),var(--blue))}

/* Footer */
.footer-bg{left:0;top:4150px;width:1200px;height:571px;background:var(--navy-deep)}
.footer-brand{left:0;width:1200px;top:4250px;text-align:center;color:var(--white);font-size:28px;font-weight:700;letter-spacing:1px}
.footer-brand i{display:inline-block;width:14px;height:14px;border-radius:50%;background:var(--orange);margin-right:12px;vertical-align:middle}
.fcol h4{font-size:20px;font-weight:600;color:var(--white);margin-bottom:12px}
.fcol li{list-style:none;font-size:11.5px;line-height:22.5px;color:#dfe4f0}
.fcol li svg{vertical-align:-1px;margin-right:6px}
.socials{display:flex;gap:14px;margin-top:10px;padding-left:10px}
.socials span{width:8px;height:8px;border-radius:50%;background:#dfe4f0}
.f-line{left:76px;top:4653px;width:1050px;height:1px;background:rgba(255,255,255,.25)}
.copy{left:0;width:1200px;top:4676px;text-align:center;font-size:12px;color:#dfe4f0}
.to-top{left:1145px;top:4637px;width:34px;height:34px;border-radius:50%;background:linear-gradient(135deg,var(--orange-light),var(--red));display:flex;align-items:center;justify-content:center}
</style>
</head>
<body>

<!-- Hero -->
<section class="hero abs">
  <div class="hero-photo abs" role="img" aria-label="Technician in a grey shirt and cap repairing a wall-mounted air conditioner with pliers and a screwdriver"></div>
  <h1 class="abs">Quality Air<br>Conditioning Repairs,<br>Service, &amp; Installations</h1>
  <p class="hero-text abs">Our service is second to none; we have a team of experienced technicians that consistently deliver the best quality air conditioner repairs Perth has to offer.</p>
  <a class="btn btn-book abs">Book A Service</a>
</section>

<svg class="swoosh abs" style="top:760px" width="1200" height="220" viewBox="0 0 1200 220" aria-hidden="true">
  <defs><linearGradient id="bandA" x1="0" x2="1"><stop offset="0" stop-color="#EE7325"/><stop offset=".45" stop-color="#F0912C"/><stop offset=".6" stop-color="#2a5fa3"/><stop offset="1" stop-color="#0677BA"/></linearGradient></defs>
  <path d="M0 150 Q520 -20 1200 60 L1200 220 L0 220Z" fill="url(#bandA)"/>
  <path d="M0 205 Q560 20 1200 120 L1200 220 L0 220Z" fill="#fff"/>
</svg>

<!-- Header -->
<div class="nav-bar abs"></div>
<div class="brand abs">Breezeline Climate WA</div>
<nav class="nav-links abs">
  <svg class="home-ico" viewBox="0 0 16 14"><path d="M8 0 L16 7 H13 V14 H10 V9 H6 V14 H3 V7 H0Z" fill="#EE7325"/></svg>
  <a>About Us</a><a>Services</a><a>Cleaning</a><a>Regasing</a><a>Commissioning</a><a>Air Balancing</a>
</nav>
<a class="btn btn-quote abs">Request Quote</a>

<!-- About -->
<section class="about">
  <div class="about-photo abs" role="img" aria-label="Technician in a checked shirt testing a wall air conditioner with a multimeter"></div>
  <span class="tag about-tag abs">About Us</span>
  <h2 class="h2 abs">Need a technician?</h2>
  <p class="about-text abs">Our call out fee includes the first half hour on site. In most cases will be able to diagnose the problem with in that time, and repair it if no parts are required. If any parts, gas or additional labour is required, we will let you know before we proceed.</p>
  <div class="contact-mini abs" style="left:661px"><span class="dot" style="background:linear-gradient(135deg,#F0912C,#d8322e)"></span><div><b>Call Us</b>0412 555 318</div></div>
  <div class="contact-mini abs" style="left:790px"><span class="dot" style="background:linear-gradient(135deg,#0054AA,#1c2b5e)"></span><div><b>Email Us</b>info@breezelineclimatewa.com.au</div></div>
  <a class="btn btn-more abs">More About Us</a>
</section>

<!-- Services -->
<section class="services">
  <span class="tag svc-tag abs">Some of our speciality</span>
  <h2 class="h2 abs">Our Services</h2>
  <p class="svc-text abs">Please Be aware that paying for your service upfront does not mean next day service. Your service will however be prioritised and scheduled into the next available slot.</p>

  <div class="card feature abs" style="left:570px;top:1392px;width:230px;height:251px">
    <div class="card-photo" role="img" aria-label="Rooftop commercial air conditioning units"></div>
    <div style="padding:0 16px">Commercial Air Conditioning Installation &amp; Repairs</div>
  </div>
  <div class="card abs" style="left:812px;top:1392px;width:228px;height:78px"><span class="ico"><svg width="26" height="16"><rect x="1" y="1" width="24" height="11" rx="2" fill="none" stroke="#fff" stroke-width="2"/><line x1="5" y1="14" x2="21" y2="14" stroke="#fff" stroke-width="2"/></svg></span>Domestic aircon installation &amp; repairs</div>
  <div class="card abs" style="left:812px;top:1478px;width:228px;height:78px"><span class="ico"><svg width="24" height="24"><circle cx="12" cy="12" r="8" fill="none" stroke="#fff" stroke-width="2"/><circle cx="12" cy="12" r="3" fill="#fff"/></svg></span>Chiller Service<br>&amp; Repairs</div>
  <div class="card abs" style="left:812px;top:1565px;width:228px;height:78px"><span class="ico"><svg width="24" height="24"><path d="M6 4 V20 M12 8 V20 M18 4 V20" stroke="#fff" stroke-width="2"/></svg></span>Air quality<br>control</div>
  <div class="card abs" style="left:570px;top:1652px;width:230px;height:79px"><span class="ico"><svg width="22" height="24"><rect x="2" y="2" width="18" height="20" rx="2" fill="none" stroke="#fff" stroke-width="2"/><path d="M6 8 H16 M6 12 H16 M6 16 H12" stroke="#fff" stroke-width="2"/></svg></span>BMS upgrades<br>&amp; installation</div>
  <div class="card abs" style="left:812px;top:1652px;width:228px;height:79px"><span class="ico"><svg width="22" height="24"><rect x="2" y="2" width="18" height="20" rx="2" fill="none" stroke="#fff" stroke-width="2"/><path d="M6 8 H16 M6 12 H16 M6 16 H12" stroke="#fff" stroke-width="2"/></svg></span>BMS upgrades<br>&amp; installation</div>
</section>

<!-- Why choose -->
<div class="why-bg abs"></div>
<svg class="swoosh abs" style="top:1830px" width="1200" height="320" viewBox="0 0 1200 320" aria-hidden="true">
  <defs><linearGradient id="bandB" x1="0" x2="1"><stop offset="0" stop-color="#EE7325"/><stop offset=".4" stop-color="#F0912C"/><stop offset=".62" stop-color="#2a5fa3"/><stop offset="1" stop-color="#0677BA"/></linearGradient></defs>
  <path d="M0 230 Q600 -130 1200 210 L1200 320 L0 320Z" fill="url(#bandB)"/>
  <path d="M0 320 Q600 -80 1200 320Z" fill="#f2f2f2"/>
</svg>
<section class="why">
  <span class="tag why-tag abs">Why choose us</span>
  <h2 class="h2 abs">Cool Reasons to Choose Us</h2>
  <div class="reason abs" style="left:111px;top:2102px"><div class="ring"><div class="num">01</div><svg class="arrow" width="30" height="10"><path d="M0 5 H26 M21 1 L27 5 L21 9" stroke="#EE7325" fill="none" stroke-width="1.5"/></svg></div><h3>Local<br>Experts</h3><p>We know WA's climate inside out.</p></div>
  <div class="reason abs" style="left:309px;top:2096px"><div class="ring"><div class="num">02</div><svg class="arrow" width="30" height="10"><path d="M0 5 H26 M21 1 L27 5 L21 9" stroke="#EE7325" fill="none" stroke-width="1.5"/></svg></div><h3>Friendly, Reliable Service</h3><p>Respectful, caring, &amp; always with a smile.</p></div>
  <div class="reason abs" style="left:509px;top:2102px"><div class="ring"><div class="num">03</div><svg class="arrow" width="30" height="10"><path d="M0 5 H26 M21 1 L27 5 L21 9" stroke="#EE7325" fill="none" stroke-width="1.5"/></svg></div><h3>Quality<br>Workmanship</h3><p>Every job done to the highest standard.</p></div>
  <div class="reason abs" style="left:706px;top:2096px"><div class="ring"><div class="num warm">04</div><svg class="arrow" width="30" height="10"><path d="M0 5 H26 M21 1 L27 5 L21 9" stroke="#EE7325" fill="none" stroke-width="1.5"/></svg></div><h3>Upfront<br>Pricing</h3><p>Clear quotes, no hidden costs.</p></div>
  <div class="reason abs" style="left:904px;top:2102px"><div class="ring"><div class="num">05</div><svg class="arrow" width="30" height="10"><path d="M0 5 H26 M21 1 L27 5 L21 9" stroke="#EE7325" fill="none" stroke-width="1.5"/></svg></div><h3>Fast Response<br>Times</h3><p>Quick help, any season.</p></div>
</section>

<!-- Testimonials -->
<svg class="swoosh abs" style="top:2380px" width="1200" height="200" viewBox="0 0 1200 200" aria-hidden="true">
  <path d="M0 200 L0 190 Q500 30 1200 40 L1200 200Z" fill="#fff"/>
</svg>
<section class="testi">
  <span class="tag testi-tag abs">Testimonials</span>
  <h2 class="h2 abs">What Our Clients Says</h2>
  <div class="quote-badge abs"><svg width="44" height="34" viewBox="0 0 44 34"><path d="M0 34 V18 Q0 4 14 0 L16 5 Q8 8 8 16 H18 V34Z M24 34 V18 Q24 4 38 0 L40 5 Q32 8 32 16 H42 V34Z" fill="#fff"/></svg></div>
  <svg class="abs" style="left:272px;top:2640px" width="96" height="70" viewBox="0 0 96 70" aria-hidden="true"><path d="M0 70 V38 Q0 8 30 0 L34 10 Q16 16 16 34 H38 V70Z M50 70 V38 Q50 8 80 0 L84 10 Q66 16 66 34 H88 V70Z" fill="#e9edf3"/></svg>
  <p class="testi-text abs">Please thank Marcus for his professionalism and honesty. He advised us that a service was not required after checking over everything and fixed other items.</p>
  <div class="stars abs">★★★★★</div>
  <div class="testi-name abs">Renee Holloway</div>
  <div class="dots abs"><span></span><span></span><span></span></div>
  <div class="divider abs"></div>
</section>

<!-- FAQ -->
<section class="faq">
  <h2 class="h2 abs">FAQs</h2>
  <div class="faq-list abs">
    <div class="faq-item">Which areas do you service?<span>+</span></div>
    <div class="faq-item">Do you offer free quotes?<span>+</span></div>
    <div class="faq-item">How often should I service my air conditioner?<span>+</span></div>
    <div class="faq-item">What brands do you work with?<span>+</span></div>
    <div class="faq-item">Do you have emergency repair services?<span>+</span></div>
  </div>
  <div class="faq-visual abs" role="img" aria-label="White split system air conditioner with warm and cool airflow graphics"></div>
</section>

<!-- Contact -->
<section class="contact">
  <form class="contact-card abs">
    <h2>Contact Us</h2>
    <div class="field" style="top:119px">Name</div>
    <div class="field" style="top:172px">Email</div>
    <div class="field area" style="top:226px">Message</div>
    <div class="submit">Submit Now</div>
  </form>
  <div class="cta">
    <h2 class="h2 abs">Need a technician?</h2>
    <p class="abs">Our call out fee includes the first half hour on site. In most cases will be able to diagnose the problem with in that time, and repair it if no parts are required. If any parts, gas or additional labour is required, we will let you know before we proceed.</p>
    <a class="btn btn-sm abs" style="left:624px;width:142px">Book A Services</a>
    <a class="btn btn-sm btn-blue abs" style="left:776px;width:142px">Request Quote</a>
  </div>
</section>

<!-- Footer -->
<svg class="swoosh abs" style="top:4060px" width="1200" height="200" viewBox="0 0 1200 200" aria-hidden="true">
  <defs><linearGradient id="bandC" x1="0" x2="1"><stop offset="0" stop-color="#EE7325"/><stop offset=".45" stop-color="#F0912C"/><stop offset=".6" stop-color="#2a5fa3"/><stop offset="1" stop-color="#0677BA"/></linearGradient></defs>
  <path d="M0 140 Q600 -20 1200 110 L1200 200 L0 200Z" fill="url(#bandC)"/>
  <path d="M0 200 L0 190 Q600 30 1200 180 L1200 200Z" fill="#1d2a57"/>
</svg>
<footer>
  <div class="footer-bg abs"></div>
  <div class="footer-brand abs"><i></i>Breezeline Climate Services WA</div>
  <div class="fcol abs" style="left:136px;top:4395px">
    <h4>Extra Links</h4>
    <ul><li>Home</li><li>About</li><li>Service</li><li>Project Works</li><li>Residential Services</li><li>Careers</li><li>Contact</li></ul>
  </div>
  <div class="fcol abs" style="left:335px;top:4395px">
    <h4>Services</h4>
    <ul><li>Commercial Air Conditioning Installation &amp; Repairs</li><li>Domestic Aircon Installation &amp; Repairs</li><li>Coolroom Installation &amp; Repairs</li><li>Chiller Service &amp; Repairs</li><li>Air Quality Control</li><li>BMS Upgrades &amp; Installation</li></ul>
  </div>
  <div class="fcol abs" style="left:681px;top:4395px">
    <h4>Contact Us</h4>
    <ul>
      <li><svg width="8" height="10"><path d="M4 0 A4 4 0 0 1 8 4 Q8 6 4 10 Q0 6 0 4 A4 4 0 0 1 4 0Z" fill="#EE7325"/></svg>42 Harbour Lane, Canning Vale WA 6155</li>
      <li><svg width="10" height="8"><rect width="10" height="8" rx="1" fill="#EE7325"/></svg>info@breezelineclimatewa.com.au</li>
      <li><svg width="9" height="9"><path d="M1 0 L3 0 L4 3 L2.5 4 Q4 6 5 6.5 L6 5 L9 6 L9 8 Q8 9 7 9 Q0 8 0 2 Q0 1 1 0Z" fill="#EE7325"/></svg>0412 555 318</li>
      <li style="line-height:17px;margin-top:3px"><svg width="9" height="9"><circle cx="4.5" cy="4.5" r="4.5" fill="#EE7325"/></svg>Mon–Fri: 8.00am to 5.00pm<br><span style="padding-left:15px">Weekends and Public Holidays:</span><br><span style="padding-left:15px">Additional Callout Fee.</span></li>
    </ul>
    <div class="socials"><span></span><span></span><span></span></div>
  </div>
  <div class="fcol abs" style="left:964px;top:4395px">
    <h4>Info</h4>
    <ul><li>Terms &amp; Conditions</li><li>Privacy Policy</li><li>Contact Us</li></ul>
  </div>
  <div class="f-line abs"></div>
  <div class="to-top abs"><svg width="10" height="6"><path d="M1 5 L5 1 L9 5" stroke="#fff" fill="none" stroke-width="1.6"/></svg></div>
  <p class="copy abs">Copyright © 2025 Breezeline Climate Services WA All Right Reserved &nbsp; AU48213</p>
</footer>

</body>
</html>
```